I want ideas sample designs for my book cover

Hello,

We need a book cover designed in flat and 3D Versions. We would like to have jpg and png for final output and include a copy of the PSD for future revisions.

Here are the basic details:

Title: The Harvest of Quiet Builders
Author: Norman Quillfeather

Dimensions of book:

Was looking at the Pavo website for dimensions. I thought you may want to go on there and look at the different sizes. I used the 6x9” perfect bound US trade size for my book. You will see that this has a spine width of 0.225”, Cover size of 12.48 x 9.25” and spine begins at 6.125”

If you need background info on the author just to get an idea what he does, please check:

http://NormanQuillfeather.example

IMPORTANT: Please see attached document for a more detailed info:

Exact Title Of book
Back Cover
Spine Info
Measurements of book and dimension
Examples of book covers
Norman's photo attached

Thanks,
Darlene

Industry/Entity Type

Life Coaching

Font styles to use
Serif

Requirements
Must have
• Jpg, png and PSD files
• title
• author
• exact dimensions
• front and back cover
• flat and 3d versions

```html
<!DOCTYPE html>
<html lang="en">
<head>
<meta charset="utf-8">
<title>The Harvest of Quiet Builders — Norman Quillfeather</title>
<link rel="stylesheet" href="https://fonts.googleapis.com/css2?family=Oswald:wght@500;600&family=Roboto:wght@300&display=swap">
<style>
  :root {
    --chalkboard-top: #2f4a66;
    --chalkboard-mid: #5d7891;
    --chalkboard-low: #8fa6b8;
    --paper: #ffffff;
    --navy: #173f6e;
    --navy-deep: #112f55;
    --band-dark: #16335a;
    --band-light: #245d99;
    --ink-dark: #0f1f33;
    --floor-top: #b9c8d2;
    --floor-bottom: #6f8797;
  }
  html, body { margin: 0; padding: 0; overflow: hidden; background: #ffffff; }
  .cover {
    position: relative;
    width: 794px;
    height: 1200px;
    overflow: hidden;
    background: var(--paper);
  }
  .backdrop {
    position: absolute; left: 0; top: 0; width: 794px; height: 1028px;
    background: radial-gradient(ellipse at 55% 60%, var(--chalkboard-low) 0%, var(--chalkboard-mid) 40%, var(--chalkboard-top) 100%);
  }
  .floor {
    position: absolute; left: 0; top: 1028px; width: 794px; height: 172px;
    background: linear-gradient(180deg, var(--floor-top) 0%, var(--floor-bottom) 100%);
  }
  .title-band {
    position: absolute; left: 0; top: 370px; width: 648px; height: 322px;
    background: rgba(255,255,255,0.96);
  }
  .tagline-band {
    position: absolute; left: 0; top: 692px; width: 648px; height: 150px;
    background: linear-gradient(90deg, var(--band-dark) 0%, var(--band-dark) 45%, var(--band-light) 100%);
  }
  .author-band {
    position: absolute; left: 0; top: 842px; width: 648px; height: 186px;
    background: var(--paper);
  }
  .figure {
    position: absolute; left: 600px; top: 340px; width: 170px; height: 745px;
    background: linear-gradient(180deg, #c9a98c 0%, #d8dde4 18%, #b4bcc6 45%, #2a2d33 60%, #1b1d22 100%);
    border-radius: 60px 60px 10px 10px;
  }
  .title {
    position: absolute; right: 250px; top: 412px; margin: 0;
    font-family: "Oswald", "Arial Narrow", sans-serif;
    font-weight: 500;
    font-size: 86px;
    line-height: 82px;
    letter-spacing: -1px;
    text-align: right;
    text-transform: uppercase;
    color: var(--navy);
  }
  .title span { display: block; white-space: nowrap; }
  .tagline {
    position: absolute; right: 250px; top: 714px; margin: 0;
    font-family: "Roboto", Arial, sans-serif;
    font-weight: 300;
    font-size: 21.5px;
    line-height: 31px;
    text-align: right;
    color: #ffffff;
    white-space: nowrap;
  }
  .credit {
    position: absolute; right: 250px; top: 878px; margin: 0;
    font-family: "Oswald", "Arial Narrow", sans-serif;
    font-weight: 500;
    font-size: 24px;
    line-height: 30px;
    letter-spacing: -0.3px;
    text-transform: uppercase;
    color: var(--ink-dark);
    text-align: right;
    white-space: nowrap;
  }
  .credit .accent { color: var(--band-light); }
  .author {
    position: absolute; right: 250px; top: 922px; margin: 0;
    font-family: "Oswald", "Arial Narrow", sans-serif;
    font-weight: 600;
    font-size: 54px;
    line-height: 66px;
    letter-spacing: -0.5px;
    text-transform: uppercase;
    color: var(--navy-deep);
    text-align: right;
    white-space: nowrap;
  }
</style>
</head>
<body>
  <div class="cover">
    <div class="backdrop" role="img" aria-label="Chalkboard covered with hand-drawn business sketches: clouds, arrows, charts, a light bulb and words like money, income and success"></div>
    <div class="floor" role="img" aria-label="Soft grey-blue floor fading into the distance"></div>

    <div class="title-band"></div>
    <div class="tagline-band"></div>
    <div class="author-band"></div>

    <div class="figure" role="img" aria-label="Businesswoman in a striped blouse and dark trousers standing in profile, holding a black briefcase"></div>

    <h1 class="title">
      <span>The Harvest</span>
      <span>of Quiet</span>
      <span>Builders</span>
    </h1>

    <p class="tagline">
      How this ancient wisdom is helping billionaires,<br>
      industry icons and entrepreneurs to be better<br>
      leaders, increase impact and leave a legacy.
    </p>

    <p class="credit">From the <span class="accent">best selling</span> author of “Lanterns”</p>
    <p class="author">Norman Quillfeather</p>
  </div>
</body>
</html>
```